brovlanepass.net

Develop a website for brolanepass.net will be a site to sell tickets for concerts, shows, shows, theaters and others. I need a web design easy view, very easy to use and accumulate events by date. The aim is to develop the site was connected to a complex system that is already developed. (Important this page to a robust system was connected via links the idea is to develop only the front view)
Updates

Reason: I need more designs yet we have not made the decision

Target Market(s)

millennials, adults, who want to enjoy concerts and shows

Industry/Entity Type

Event

Number of Pages Required

5+ page

Colors
1b1b1b
aaaaaa
ffffff

Requirements
Must have
• Easy Vista, accumulation of upcoming events, past events. The tabs should have are: 1 Start: In this part of upcoming events occur. You could put a banner on the top and down the events by date. 2. How to order: page with instructions on how to purchase tickets 3. About Us: The company history 4. Contact: Phones and template for contact by mail 5. Our policies: shopping 6. Notice Privacy: Privacy Notice Copoy 7. Centers Sale: physical places where they can purchase tickets Promoters 8. access: Link to a template
Nice to have
• as you can see p www.quimbarostage.net or farunda.net or farunda.org or gallowmerk.net (important this page to a robust system was connected via links the idea is to develop only the front view)
Should not have
• Many things Tangled

```html
<!DOCTYPE html>
<html lang="en">
<head>
<meta charset="utf-8">
<title>Brovlane Pass</title>
<link rel="stylesheet" href="https://fonts.googleapis.com/css2?family=Open+Sans:wght@400;600;700&family=Roboto+Condensed:wght@400;700&family=Cabin:wght@500;600&display=swap">
<style>
:root{
  --ink:#1b1b1b;
  --ink-soft:#2a2a2a;
  --grey:#aaaaaa;
  --grey-text:#666666;
  --paper:#ffffff;
  --mist:#f3f3f3;
  --gold:#ffd54f;
  --gold-deep:#f5c324;
  --footer:#1e1e1e;
}
*{margin:0;padding:0;box-sizing:border-box}
html,body{width:1200px;height:2387px;overflow:hidden}
body{position:relative;background:var(--paper);font-family:"Open Sans",Arial,sans-serif;color:var(--ink)}
.abs{position:absolute}

/* header */
.site-header{left:0;top:0;width:1200px;height:96px;background:var(--ink)}
.brand{left:99px;top:24px;display:flex;align-items:center;gap:12px}
.brand-mark{width:42px;height:42px;background:var(--gold);border-radius:4px}
.brand-name{font-family:"Open Sans",sans-serif;font-weight:700;font-size:30px;color:var(--gold)}
.main-nav{right:200px;top:41px;display:flex;gap:17px;font-family:"Roboto Condensed",sans-serif;font-size:12.5px;color:var(--paper);text-transform:uppercase;white-space:nowrap}
.sign-in{left:1019px;top:33px;width:82px;height:31px;background:var(--gold);color:var(--ink);font-family:"Roboto Condensed",sans-serif;font-size:13px;display:flex;align-items:center;justify-content:center;border-radius:2px}

/* hero */
.hero{left:0;top:96px;width:1200px;height:533px;background:radial-gradient(ellipse at 50% 20%,#d9cbb0 0%,#8a7560 28%,#3a2d24 60%,#120d0a 100%)}
.hero-title{left:0;top:160px;width:1200px;text-align:center;font-family:"Roboto Condensed",sans-serif;font-weight:700;font-size:50px;color:var(--paper);text-shadow:0 2px 6px rgba(0,0,0,.5)}
.hero-sub{left:400px;top:226px;width:400px;text-align:center;font-size:13px;line-height:21px;color:var(--paper)}
.hero-arrow{top:327px;width:34px;height:34px;border-radius:50%;background:rgba(0,0,0,.75);display:flex;align-items:center;justify-content:center}

/* events */
.events-head{left:132px;top:492px;width:936px;height:76px;background:var(--gold);display:flex;align-items:center;justify-content:center;font-family:"Cabin",sans-serif;font-weight:600;font-size:22px;letter-spacing:.5px}
.events-row{left:99px;top:568px;width:1002px;height:268px;display:flex}
.event-card{width:200.4px;height:268px;position:relative}
.event-feature{background:linear-gradient(160deg,#3a2f35,#1a1418);color:var(--paper);text-align:center;padding-top:58px}
.event-feature h3{font-family:"Roboto Condensed",sans-serif;font-weight:400;font-size:15px}
.event-feature .date{font-family:"Roboto Condensed",sans-serif;font-size:15px;margin-top:12px}
.event-feature p{font-size:11px;line-height:17px;margin:10px 18px 0}
.book-now{display:inline-block;margin-top:16px;border:1.5px solid var(--paper);border-radius:14px;padding:4px 14px;font-size:10.5px;font-weight:600}
.events-foot{left:132px;top:836px;width:936px;height:60px;background:var(--gold);display:flex;align-items:center;justify-content:center;gap:4px}

/* welcome */
.welcome-title{left:0;top:966px;width:1200px;text-align:center;font-family:"Cabin",sans-serif;font-weight:500;font-size:36px}
.welcome-text{left:168px;top:1024px;width:864px;text-align:center;font-size:11px;line-height:22px;color:var(--grey-text)}
.feature{top:1146px;width:330px;height:120px}
.feature-icon{left:0;top:0;width:72px;height:72px;border:2px solid var(--ink);border-radius:50%;display:flex;align-items:center;justify-content:center}
.feature h4{position:absolute;left:96px;top:0;font-family:"Open Sans",sans-serif;font-weight:400;font-size:15px;text-transform:uppercase}
.feature p{position:absolute;left:96px;top:28px;width:220px;font-size:11px;line-height:20px;color:var(--grey-text)}
.read-more{position:absolute;left:96px;top:102px;font-size:11px;text-transform:uppercase;color:var(--ink-soft)}

/* blog */
.blog-band{left:0;top:1345px;width:1200px;height:528px;background:var(--mist)}
.blog-title{left:0;top:1402px;width:1200px;text-align:center;font-family:"Roboto Condensed",sans-serif;font-weight:400;font-size:31px}
.post{top:1474px;width:310px;height:330px}
.post-photo{position:absolute;left:0;top:0;width:310px;height:180px}
.post-marker{position:absolute;left:10px;top:208px;width:28px;height:28px;background:var(--gold);transform:rotate(45deg)}
.post-line{position:absolute;left:23px;top:240px;width:2px;height:80px;background:var(--gold)}
.post h5{position:absolute;left:66px;top:200px;font-weight:400;font-size:15px}
.post .meta{position:absolute;left:66px;top:232px;font-size:11.5px;color:var(--ink-soft)}
.post p{position:absolute;left:66px;top:264px;width:236px;font-size:11px;line-height:21px;color:var(--grey-text)}

/* partners */
.partners{left:99px;top:1928px;width:1002px;height:46px;display:flex;justify-content:space-between;align-items:center}
.partner{height:34px;background:#c9c9c9;border-radius:3px}

/* footer */
.site-footer{left:0;top:2024px;width:1200px;height:363px;background:var(--footer)}
.foot-brand{left:99px;top:2082px;display:flex;align-items:center;gap:12px}
.foot-brand .brand-name{font-size:28px}
.contact-row{left:99px;display:flex;gap:16px;font-size:12.5px;line-height:20px;color:var(--paper)}
.foot-head{top:2072px;font-family:"Open Sans",sans-serif;font-weight:600;font-size:15.5px;text-transform:uppercase;color:var(--paper)}
.signup-text{left:409px;top:2110px;width:290px;font-size:11px;line-height:20px;color:var(--paper)}
.signup-input{left:409px;top:2163px;width:286px;height:41px;background:var(--paper);color:var(--grey-text);font-size:11.5px;padding:12px}
.subscribe{left:409px;top:2215px;width:100px;height:41px;background:var(--gold);color:var(--ink);font-weight:700;font-size:11.5px;display:flex;align-items:center;justify-content:center}
.quick-links{left:791px;top:2114px;list-style:none;font-size:12px;line-height:24px;color:var(--paper)}
.social{left:984px;top:2114px;list-style:none;font-size:13.5px;color:var(--paper)}
.social li{display:flex;align-items:center;gap:12px;height:37px}
.social .dot{width:25px;height:25px;border:1.5px solid var(--paper);border-radius:50%}
.copyright{left:0;top:2344px;width:1200px;text-align:center;font-size:12px;color:var(--paper)}
</style>
</head>
<body>

<header class="site-header abs"></header>
<div class="brand abs"><span class="brand-mark"></span><span class="brand-name">Brovlane Pass</span></div>
<nav class="main-nav abs"><span>Home</span><span>How to order</span><span>About us</span><span>Policies</span><span>Privacy</span><span>Center sale</span><span>Access</span><span>Contact us</span></nav>
<div class="sign-in abs">SIGN IN</div>

<section class="hero abs" role="img" aria-label="Concert crowd with raised hands under warm stage light"></section>
<h1 class="hero-title abs">BROVLANE PASS</h1>
<p class="hero-sub abs">Sed ut perspiciatis unde omnis iste natus error sit voluptatem accusantium doloremque laudantium, totam</p>
<div class="hero-arrow abs" style="left:32px"><svg width="12" height="14" viewBox="0 0 12 14"><path d="M9 1 3 7l6 6" fill="none" stroke="#fff" stroke-width="2.5"/></svg></div>
<div class="hero-arrow abs" style="left:1130px"><svg width="12" height="14" viewBox="0 0 12 14"><path d="M3 1l6 6-6 6" fill="none" stroke="#fff" stroke-width="2.5"/></svg></div>

<div class="events-head abs">&#9733;&#9733;&#9733;&nbsp; UPCOMING EVENTS &nbsp;&#9733;&#9733;&#9733;</div>
<div class="events-row abs">
  <div class="event-card" role="img" aria-label="Rock band playing guitars on stage" style="background:linear-gradient(160deg,#5c7a6e,#3b4a44 55%,#b8b0a6)"></div>
  <div class="event-card event-feature">
    <h3>SED UT PERSPICIATIS</h3>
    <div class="date">MARCH17 2017</div>
    <p>Lorem ipsum dolor sit amet, consectetur adipiscing elit, sed do eiusmod</p>
    <span class="book-now">BOOK NOW!</span>
  </div>
  <div class="event-card" role="img" aria-label="Young ballet dancer facing a lit theatre stage" style="background:radial-gradient(ellipse at 50% 30%,#c89a5a,#5a3a2c 55%,#1e1410)"></div>
  <div class="event-card" role="img" aria-label="Jazz concert poster on a starry purple background" style="background:radial-gradient(circle at 50% 45%,#f2e6dc 0 22%,#5a2e6e 40%,#241232)"></div>
  <div class="event-card" role="img" aria-label="Audience watching a film in 3D glasses" style="background:linear-gradient(160deg,#8a6a5a,#3e3640 60%,#1c1a22)"></div>
</div>
<div class="events-foot abs">
  <svg width="42" height="20" viewBox="0 0 42 20"><circle cx="10" cy="10" r="8.5" fill="none" stroke="#1b1b1b" stroke-width="1.3"/><path d="M12 6 8 10l4 4" fill="none" stroke="#1b1b1b" stroke-width="1.3"/><circle cx="32" cy="10" r="8.5" fill="none" stroke="#1b1b1b" stroke-width="1.3"/><path d="M30 6l4 4-4 4" fill="none" stroke="#1b1b1b" stroke-width="1.3"/></svg>
</div>

<h2 class="welcome-title abs">Welcome To Brovlane Pass</h2>
<p class="welcome-text abs">Sed ut perspiciatis unde omnis iste natus error sit voluptatem accusantium doloremque laudantium, totam rem aperiam, eaque ipsa quae ab illo inventore veritatis et quasi architecto beatae vitae dicta sunt explicabo. Nemo enim ipsam voluptatem quia voluptas sit aspernatur aut odit aut fugit, sed quia consequuntur magni dolores eos qui ratione voluptatem sequi nesciunt. Neque porro quisquam est, qui dolorem ipsum quia dolor sit amet, consectetur</p>

<div class="feature abs" style="left:99px">
  <div class="feature-icon abs"><svg width="32" height="28" viewBox="0 0 32 28"><path d="M3 10h6l14-7v22L9 18H3z" fill="none" stroke="#1b1b1b" stroke-width="2.2" stroke-linejoin="round"/><path d="M9 18l2 8h4l-2-8" fill="none" stroke="#1b1b1b" stroke-width="2"/><path d="M27 10v6" stroke="#1b1b1b" stroke-width="2.2"/></svg></div>
  <h4>Concerts</h4>
  <p>Sed ut perspiciatis unde omnis iste natus error sit voluptatem accusantium doloremque laudantium.</p>
  <span class="read-more">Read more &#10141;</span>
</div>
<div class="feature abs" style="left:450px">
  <div class="feature-icon abs"><svg width="34" height="34" viewBox="0 0 34 34"><path d="M12 4 30 22 22 30 4 12z" fill="none" stroke="#1b1b1b" stroke-width="2.2" stroke-linejoin="round"/><path d="M12 14l8 8M15 11l8 8" stroke="#1b1b1b" stroke-width="1.6"/></svg></div>
  <h4>Shows</h4>
  <p>Sed ut perspiciatis unde omnis iste natus error sit voluptatem accusantium doloremque laudantium.</p>
  <span class="read-more">Read more &#10141;</span>
</div>
<div class="feature abs" style="left:800px">
  <div class="feature-icon abs"><svg width="38" height="30" viewBox="0 0 38 30"><path d="M2 3c6 3 12 3 18 0v10c0 7-4 11-9 11S2 20 2 13z" fill="#1b1b1b"/><path d="M18 9c6 3 12 3 18 0v10c0 7-4 10-9 10s-9-3-9-10z" fill="#1b1b1b" stroke="#fff" stroke-width="1.5"/><circle cx="7" cy="10" r="1.8" fill="#fff"/><circle cx="15" cy="10" r="1.8" fill="#fff"/><circle cx="23" cy="16" r="1.8" fill="#fff"/><circle cx="31" cy="16" r="1.8" fill="#fff"/></svg></div>
  <h4>Theaters &amp; Others</h4>
  <p>Sed ut perspiciatis unde omnis iste natus error sit voluptatem accusantium doloremque laudantium.</p>
  <span class="read-more">Read more &#10141;</span>
</div>

<section class="blog-band abs"></section>
<h2 class="blog-title abs">LATEST BLOG</h2>
<article class="post abs" style="left:99px">
  <div class="post-photo" role="img" aria-label="DJ at the decks with people dancing under red light" style="background:linear-gradient(120deg,#c8a23a,#8a2a2a 50%,#2a1a2a)"></div>
  <span class="post-marker"></span><span class="post-line"></span>
  <h5>Nemo enim ipsam voluptatem</h5>
  <div class="meta">Jan 21, 2017 &nbsp;&nbsp;\&nbsp;&nbsp; 2 comments</div>
  <p>Lorem ipsum dolor sit amet, consectetur adipiscing elit. Sed blandit massa vel mauris sollicitudin dignissim.</p>
</article>
<article class="post abs" style="left:446px">
  <div class="post-photo" role="img" aria-label="Woman seated in red theatre chairs" style="background:linear-gradient(180deg,#c9a870,#6a4a3a 55%,#5a1a1e)"></div>
  <span class="post-marker"></span><span class="post-line"></span>
  <h5>Nemo enim ipsam voluptatem</h5>
  <div class="meta">Jan 21, 2017 &nbsp;&nbsp;\&nbsp;&nbsp; 2 comments</div>
  <p>Lorem ipsum dolor sit amet, consectetur adipiscing elit. Sed blandit massa vel mauris sollicitudin dignissim.</p>
</article>
<article class="post abs" style="left:793px">
  <div class="post-photo" role="img" aria-label="Singer with microphone facing a large audience" style="background:linear-gradient(180deg,#2a2a2e,#4a3e36 55%,#1a1614)"></div>
  <span class="post-marker"></span><span class="post-line"></span>
  <h5>Nemo enim ipsam voluptatem</h5>
  <div class="meta">Jan 21, 2017 &nbsp;&nbsp;\&nbsp;&nbsp; 2 comments</div>
  <p>Lorem ipsum dolor sit amet, consectetur adipiscing elit. Sed blandit massa vel mauris sollicitudin dignissim.</p>
</article>

<div class="partners abs" aria-label="Partners">
  <span class="partner" style="width:66px"></span>
  <span class="partner" style="width:112px"></span>
  <span class="partner" style="width:110px"></span>
  <span class="partner" style="width:110px"></span>
  <span class="partner" style="width:82px"></span>
  <span class="partner" style="width:116px"></span>
</div>

<footer class="site-footer abs"></footer>
<div class="foot-brand abs"><span class="brand-mark"></span><span class="brand-name">Brovlane Pass</span></div>
<div class="contact-row abs" style="top:2150px">
  <svg width="18" height="22" viewBox="0 0 18 22"><path d="M9 21s7-7 7-12A7 7 0 0 0 2 9c0 5 7 12 7 12z" fill="none" stroke="#fff" stroke-width="1.6"/><circle cx="9" cy="9" r="2.5" fill="none" stroke="#fff" stroke-width="1.6"/></svg>
  <span>Brovlane Pass 120<br>Marlow Avenue Kestrel 482931</span>
</div>
<div class="contact-row abs" style="top:2203px">
  <svg width="18" height="18" viewBox="0 0 18 18"><path d="M4 1l3 4-2 2c1 3 3 5 6 6l2-2 4 3-2 3C8 17 1 10 1 3z" fill="none" stroke="#fff" stroke-width="1.4"/></svg>
  <span>Phone : &nbsp;914 2207 3150</span>
</div>
<div class="contact-row abs" style="top:2237px">
  <svg width="18" height="14" viewBox="0 0 18 14"><rect x="1" y="1" width="16" height="12" fill="none" stroke="#fff" stroke-width="1.4"/><path d="M1 1l8 7 8-7" fill="none" stroke="#fff" stroke-width="1.4"/></svg>
  <span>info@brovlanepass.net</span>
</div>

<h3 class="foot-head abs" style="left:409px">Sign up to receive email</h3>
<p class="signup-text abs">Excepteur sint occaecat cupidatat non proident, sunt in culpa qui Nemo enim ipsam voluptatem</p>
<div class="signup-input abs">Enter Name</div>
<div class="subscribe abs">SUBSCRIBE</div>

<h3 class="foot-head abs" style="left:791px">Quick links</h3>
<ul class="quick-links abs"><li>Home</li><li>About Us</li><li>How to Order</li><li>Policies</li><li>Center Sale</li><li>Privacy</li><li>Contact Us</li></ul>

<h3 class="foot-head abs" style="left:984px">Social media</h3>
<ul class="social abs">
  <li><span class="dot"></span>Friendwall</li>
  <li><span class="dot"></span>Chirpline</li>
  <li><span class="dot"></span>Circlenet</li>
  <li><span class="dot"></span>Vidstream</li>
</ul>

<p class="copyright abs">Copyright &copy; Brovlane Pass 2017. All rights reserved.</p>

</body>
</html>
```